Harrowgate Care Assurance Ltd needs a business card and logo

We need a logo for documents, invoices etc and a business card to match. We are a health auditing, training and consulting company based in NZ and working in both Australia and NZ. We ensure health organisations meet all their compliance requirements and develop expertise in the health auditing sector. The design should in some way reflect either symbols for quality management in the health sector.

Target Market(s)

Health providers and those wishing to increase their capability in meeting and understanding compliance requirements

Industry/Entity Type

Business

Contact Information for Business Card

Logo plus contact details

Logo Text

Health auditing, consultancy and training

Requirements
Must have
• Name and contact details director: Marla Fenwick, mfenwick@hca-example.co.nz, PO Box 318, Warkworth, NZ, cell +6427391652

```html
<!DOCTYPE html>
<html lang="en">
<head>
<meta charset="utf-8">
<title>Harrowgate Care Assurance Ltd — Business Card</title>
<link rel="stylesheet" href="https://fonts.googleapis.com/css2?family=Open+Sans:wght@400;600;700&display=swap">
<style>
  :root {
    --backdrop: #2b2b2b;
    --brand-blue-deep: #0a5b9c;
    --brand-blue: #0f74bf;
    --brand-blue-light: #1b86cb;
    --band-blue: #1783c8;
    --card-white: #ffffff;
    --ink-dark: #333333;
    --footer-strip: #383838;
  }
  * { box-sizing: border-box; margin: 0; padding: 0; }
  html, body {
    width: 1200px;
    height: 1002px;
    overflow: hidden;
    background: var(--backdrop);
    font-family: "Open Sans", Arial, sans-serif;
  }
  .canvas { position: relative; width: 1200px; height: 1002px; }

  .card {
    position: absolute;
    left: 275px;
    width: 619px;
    height: 379px;
    border-radius: 13px;
    overflow: hidden;
  }
  .card--front {
    top: 100px;
    background: radial-gradient(ellipse 55% 60% at 55% 50%, var(--brand-blue-light) 0%, var(--brand-blue) 45%, var(--brand-blue-deep) 100%);
  }
  .card--back {
    top: 511px;
    background: var(--card-white);
  }

  .brand-mark {
    position: absolute;
    border-radius: 50%;
  }
  .card--front .brand-mark {
    left: 124px; top: 139px; width: 108px; height: 108px;
    background: radial-gradient(circle at 40% 35%, #ffffff 0%, #f2f2f2 70%, #dcdcdc 100%);
  }
  .card--back .brand-mark {
    left: 128px; top: 84px; width: 112px; height: 112px;
    background: radial-gradient(circle at 40% 35%, #2a9be0 0%, var(--brand-blue) 60%, var(--brand-blue-deep) 100%);
  }

  .brand-name {
    position: absolute;
    text-transform: uppercase;
    line-height: 1;
    font-weight: 400;
  }
  .brand-name__main { display: block; font-size: 25px; letter-spacing: 0.5px; }
  .brand-name__sub { display: block; font-size: 13px; letter-spacing: 4px; margin-top: 8px; padding-left: 22px; }
  .card--front .brand-name { left: 250px; top: 175px; color: var(--card-white); }
  .card--back .brand-name { left: 248px; top: 124px; color: var(--ink-dark); }

  .contact-band {
    position: absolute;
    left: 0; top: 233px;
    width: 100%; height: 124px;
    background: var(--band-blue);
    color: var(--card-white);
  }
  .footer-strip {
    position: absolute;
    left: 0; top: 357px;
    width: 100%; height: 22px;
    background: var(--footer-strip);
  }
  .contact-person { position: absolute; left: 48px; top: 54px; font-size: 15.5px; line-height: 26px; }
  .contact-person__name { font-weight: 700; letter-spacing: 0.6px; text-transform: uppercase; }
  .contact-channels { position: absolute; left: 366px; top: 57px; font-size: 15.5px; line-height: 21px; }
  .contact-channels li { list-style: none; display: flex; align-items: center; gap: 6px; }
  .contact-channels svg { width: 14px; height: 14px; flex: none; }
</style>
</head>
<body>
<main class="canvas">
  <section class="card card--front" aria-label="Card front">
    <span class="brand-mark"></span>
    <h1 class="brand-name">
      <span class="brand-name__main">Harrowgate Care</span>
      <span class="brand-name__sub">Assurance Ltd</span>
    </h1>
  </section>

  <section class="card card--back" aria-label="Card back">
    <span class="brand-mark"></span>
    <h2 class="brand-name">
      <span class="brand-name__main">Harrowgate Care</span>
      <span class="brand-name__sub">Assurance Ltd</span>
    </h2>
    <div class="contact-band">
      <div class="contact-person">
        <p class="contact-person__name">Marla Fenwick</p>
        <p>PO Box 318, Warkworth, NZ</p>
      </div>
      <ul class="contact-channels">
        <li>
          <svg viewBox="0 0 14 14" aria-hidden="true"><rect x="3.5" y="1" width="7" height="12" rx="1.2" fill="none" stroke="#fff" stroke-width="1.4"/><rect x="5" y="2.8" width="4" height="7" fill="#fff"/></svg>
          <span>+6427391652</span>
        </li>
        <li>
          <svg viewBox="0 0 14 14" aria-hidden="true"><rect x="1" y="3" width="12" height="8.5" fill="#fff"/><path d="M1 3 L7 8 L13 3" fill="none" stroke="#1783c8" stroke-width="1.2"/></svg>
          <span>mfenwick@hca-example.co.nz</span>
        </li>
      </ul>
    </div>
    <div class="footer-strip"></div>
  </section>
</main>
</body>
</html>
```